Veldmark Supplies Business Card

Professional business card that stand out to our potential customers. Front and back with clean modern design

Industry/Entity Type

Oil and gas

Contact Information for Business Card

Name, address, website , office phone and cell number

Requirements
Must have
• Editable files for each employee

```html
<!DOCTYPE html>
<html lang="en">
<head>
<meta charset="utf-8">
<title>Veldmark Supplies Business Card</title>
<link href="https://fonts.googleapis.com/css2?family=Montserrat:wght@400;500;700;800&display=swap" rel="stylesheet">
<style>
  :root {
    --brand-red: #ec2127;
    --brand-blue: #08a9cf;
    --card-white: #ffffff;
    --ink: #1c1c1c;
    --backdrop: #d9d9d9;
  }
  * { box-sizing: border-box; margin: 0; padding: 0; }
  html, body { width: 1200px; height: 856px; overflow: hidden; }
  body {
    background: var(--backdrop);
    font-family: "Montserrat", sans-serif;
    display: flex;
    align-items: center;
    justify-content: center;
    gap: 40px;
  }
  .card {
    position: relative;
    width: 540px;
    height: 309px;
    overflow: hidden;
    box-shadow: 0 10px 28px rgba(0,0,0,0.25);
  }
  .card-front { background: var(--card-white); }
  .card-back { background: var(--brand-red); display: flex; align-items: center; justify-content: center; }

  .front-wave { position: absolute; inset: 0; width: 100%; height: 100%; }

  .brand-lockup {
    position: absolute;
    left: 30px;
    top: 150px;
    display: flex;
    align-items: center;
    gap: 8px;
    color: var(--brand-red);
    font-weight: 800;
    font-size: 16px;
    letter-spacing: 0.4px;
    text-transform: uppercase;
    white-space: nowrap;
  }
  .brand-square { width: 15px; height: 15px; background: var(--brand-red); flex: none; }

  .divider {
    position: absolute;
    left: 252px;
    top: 36px;
    width: 1px;
    height: 132px;
    background: var(--brand-red);
  }

  .contact {
    position: absolute;
    left: 270px;
    top: 28px;
    color: var(--ink);
    font-size: 10.5px;
    line-height: 1.35;
    white-space: nowrap;
  }
  .contact-name { color: var(--brand-red); font-weight: 800; font-size: 15px; letter-spacing: 0.3px; }
  .contact-title { margin-bottom: 8px; }
  .contact-address { margin-bottom: 7px; }
  .contact-list { list-style: none; }
  .contact-list li { display: flex; align-items: center; gap: 8px; margin-bottom: 3px; }
  .contact-icon { width: 13px; height: 13px; background: var(--brand-red); border-radius: 2px; flex: none; display: flex; align-items: center; justify-content: center; }
  .contact-icon svg { width: 9px; height: 9px; fill: none; stroke: #fff; stroke-width: 1.6; }

  .back-lockup {
    display: flex;
    align-items: center;
    gap: 14px;
    color: var(--card-white);
    font-weight: 800;
    font-size: 30px;
    letter-spacing: 1px;
    text-transform: uppercase;
    white-space: nowrap;
  }
  .back-square { width: 28px; height: 28px; background: var(--card-white); flex: none; }
</style>
</head>
<body>
  <section class="card card-front" aria-label="Business card front">
    <svg class="front-wave" viewBox="0 0 540 309" preserveAspectRatio="none" aria-hidden="true">
      <path d="M0,292 C170,294 330,208 540,206 L540,309 L0,309 Z" fill="var(--brand-red)"/>
      <path d="M0,278 C170,281 320,196 500,192" fill="none" stroke="var(--brand-blue)" stroke-width="6"/>
    </svg>

    <div class="brand-lockup"><span class="brand-square"></span>Veldmark Supplies</div>
    <div class="divider"></div>

    <div class="contact">
      <p class="contact-name">DARA WHITCOMBE</p>
      <p class="contact-title">President</p>
      <p class="contact-address">482 Harlow Ave, Ste<br>210, Midland, TX 79701</p>
      <ul class="contact-list">
        <li><span class="contact-icon"><svg viewBox="0 0 10 10"><path d="M2 1h2l1 2-1 1a5 5 0 0 0 2 2l1-1 2 1v2a1 1 0 0 1-1 1A8 8 0 0 1 1 2a1 1 0 0 1 1-1z"/></svg></span>432-555-0148</li>
        <li><span class="contact-icon"><svg viewBox="0 0 10 10"><rect x="3" y="1" width="4" height="8" rx="0.6"/></svg></span>432-555-0192</li>
        <li><span class="contact-icon"><svg viewBox="0 0 10 10"><rect x="1" y="2.5" width="8" height="5"/><path d="M1 2.5l4 3 4-3"/></svg></span>info@veldmarksupply.com</li>
        <li><span class="contact-icon"><svg viewBox="0 0 10 10"><circle cx="5" cy="5" r="4"/><path d="M1 5h8M5 1c2 2 2 6 0 8M5 1c-2 2-2 6 0 8"/></svg></span>www.veldmarksupply.com</li>
      </ul>
    </div>
  </section>

  <section class="card card-back" aria-label="Business card back">
    <div class="back-lockup"><span class="back-square"></span>Veldmark Supplies</div>
  </section>
</body>
</html>
```